Clean Modern Skin Product branding/ label.

I need a label for a skincare line. The company is Dermaloft but product names will vary. A couple products to list are:
Sensitive Cleanser, Lumeno, Repair, Halo up, Mendora, Mendora Plus, Mendora Intense, Tavelo, Balance and Vivanto.

I would like the color scheme to be muted greens, grays, tourquise. The bottles are white, boston shaped with pumps, and ounces are 2, 4, 8, 16 ounces. When I choose the design, I can give you exact label sizes. Along with the ingredience already on the product label.

The look I desire is clean, minimal. A modern, organic look. Ideas that come to mind are a Veloraine,https://www.veloraine-example.com/product/2846/37204/3-step/step-2-exfoliate/clarifying-lotion-1 and the simplicity of Bo Tarn.

Both styles high light the name, in this case Dermaloft, and then the specific product.

My product is clean utilizing pure ingredients rather that a bunch fillers and binders. When I work with my clients I normally will say we need to "restore the balance" from over use of harsh products. That is why this lines works. It restores the skin to it's natural state. The process is simple, so I would like the label to reflect that simplicity.

Target Market(s)

Anyone with sensitive skin. So gender neutral

Industry/Entity Type

Skin Care Product

Font styles to use
Serif
Sans Serif
Decorative

Colors
acd037
33b8a4
fcfefd
85cae6
d3d3d3

Requirements
Must have
• Logo, name of product and color identity for cleanser, Active products, moisturizers
• I am thinking we could have one color for a cleanser and a space where I can put a sticker on which cleanser it is. Acne Cleasner, Sensitive Cleanser, and Cleanser.
Nice to have
• Not sure....suprise me. I would like the font to stay the same on the DERMALOFT, but you can change color, or color of leaf.
Should not have
• Too busy, too crowded or look like every other skincare line

```html
<!DOCTYPE html>
<html lang="en">
<head>
<meta charset="utf-8">
<title>Dermaloft – Sensitive Cleanser Label</title>
<link href="https://fonts.googleapis.com/css2?family=Nunito+Sans:wght@300;600;800&display=swap" rel="stylesheet">
<style>
  :root {
    --label-white: #fcfefd;
    --stroke-aqua: #a9ece4;
    --stroke-aqua-soft: #c4f3ed;
    --name-gray: #4a4d50;
    --sub-gray: #6b7379;
    --rule-gray: #8c9aa3;
    --mark-green: #8fd63a;
    --mark-green-soft: #c6ee98;
    --tag-green: #8be22a;
  }
  html, body {
    margin: 0;
    padding: 0;
    width: 1200px;
    height: 1200px;
    overflow: hidden;
    background: var(--label-white);
  }
  .label {
    position: relative;
    width: 1200px;
    height: 1200px;
    background: var(--label-white);
    font-family: "Nunito Sans", sans-serif;
  }
  .brand-band {
    position: absolute;
    left: 250px;
    top: 310px;
    width: 700px;
    height: 180px;
    background: linear-gradient(90deg, var(--stroke-aqua) 0%, var(--stroke-aqua) 80%, var(--stroke-aqua-soft) 100%);
    transform: rotate(-1.2deg);
  }
  .brand-name {
    position: absolute;
    left: 0;
    right: 0;
    top: 318px;
    margin: 0;
    text-align: center;
    font-size: 132px;
    font-weight: 600;
    letter-spacing: -2px;
    line-height: 1;
    color: var(--name-gray);
    text-transform: lowercase;
  }
  .product-name {
    position: absolute;
    left: 50%;
    top: 536px;
    transform: translateX(-50%);
    margin: 0;
    padding: 6px 10px 8px;
    border-top: 2px solid var(--rule-gray);
    border-bottom: 2px solid var(--rule-gray);
    font-size: 62px;
    font-weight: 300;
    line-height: 1.1;
    color: var(--sub-gray);
    white-space: nowrap;
  }
  .mark-area {
    position: absolute;
    left: 540px;
    top: 805px;
    width: 120px;
    height: 120px;
    background: radial-gradient(circle at 50% 50%, var(--mark-green) 0%, var(--mark-green-soft) 100%);
  }
  .tagline {
    position: absolute;
    left: 0;
    right: 0;
    top: 938px;
    margin: 0;
    text-align: center;
    font-size: 44px;
    font-weight: 800;
    line-height: 1.2;
    color: var(--tag-green);
  }
</style>
</head>
<body>
  <main class="label">
    <div class="brand-band" role="img" aria-label="Soft aqua brush stroke behind the brand name"></div>
    <h1 class="brand-name">Dermaloft</h1>
    <h2 class="product-name">Sensitive Cleanser</h2>
    <div class="mark-area" role="img" aria-label="Space for the green brand symbol"></div>
    <p class="tagline">restore the balance</p>
  </main>
</body>
</html>
```